Flyer für Schulungen für Unternehmen
Zielgruppe
Wir machen Schulungen für Unternehmen zum Thema Logistik, Arbeitsmittelprüfung und Betriebssicherheit.
Aufgabenstellung
Wir haben eine neue Förderung erhalten für unsere Weiterbildung nach dem BKrFQG.
Wir können nun Schulungen ab 40€ abieten und wollen dafür Werbung gestalten. Wir möchten einen Fyler nur zum Thema Schulungen bei der Kolbe Academy.

```html
<!DOCTYPE html>
<html lang="de">
<head>
<meta charset="utf-8">
<title>Weiterbildung nach dem BKrFQG</title>
<link rel="stylesheet" href="https://fonts.googleapis.com/css2?family=Jost:wght@400;500;700;900&display=swap">
<style>
  :root {
    --dark: #2d2d2d;
    --light: #ececec;
    --white: #ffffff;
    --ink: #1a1a1a;
    --ink-on-dark: #f2f2f2;
    --rule: #1a1a1a;
    --rule-on-dark: #e6e6e6;
  }
  * { margin: 0; padding: 0; box-sizing: border-box; }
  html, body { width: 1200px; height: 848px; overflow: hidden; background: var(--white); }
  body { font-family: "Jost", "Helvetica Neue", Arial, sans-serif; color: var(--ink); }
  .flyer { position: relative; width: 1200px; height: 848px; overflow: hidden; }

  .panel { position: absolute; }
  .panel--dark { background: var(--dark); }
  .panel--light { background: var(--light); }
  .panel--white { background: var(--white); }
  .on-dark { color: var(--ink-on-dark); }

  .photo-warehouse {
    position: absolute; left: 800px; top: 0; width: 400px; height: 210px;
    background: linear-gradient(135deg, #6b5a55 0%, #9a8f8c 30%, #c9c2b8 50%, #8c6f52 70%, #3f5d86 100%);
  }
  .photo-truck {
    position: absolute; left: 0; top: 655px; width: 400px; height: 193px;
    background: linear-gradient(160deg, #6f7a5e 0%, #8f9b86 30%, #3f8a3c 55%, #d9d9d6 70%, #5d5f5a 100%);
  }

  .num { position: absolute; font-weight: 900; font-size: 56px; line-height: 1; letter-spacing: -1px; }
  .title { position: absolute; font-weight: 700; font-size: 15.5px; line-height: 22.5px; white-space: nowrap; }
  .price { position: absolute; font-size: 12.2px; line-height: 16px; white-space: nowrap; letter-spacing: 0.1px; }
  .rule { position: absolute; height: 1px; background: var(--rule); }
  .rule.on-dark { background: var(--rule-on-dark); }
  .copy { position: absolute; font-size: 12.2px; line-height: 17.1px; white-space: nowrap; letter-spacing: 0.15px; }
  .copy p + p, .copy p + ul { margin-top: 17.1px; }
  .copy p + ul.tight { margin-top: 0; }
  .modul-label { font-weight: 700; font-size: 14px; }
  .copy b { font-weight: 700; }

  .note-box {
    position: absolute; left: 428px; top: 571px; width: 344px; height: 62px;
    background: var(--dark); color: var(--ink-on-dark);
    font-size: 12.2px; line-height: 17.1px; padding: 16px 0 0 23px; white-space: nowrap;
  }
  .topics { list-style: none; margin-left: 24px; }
  .topics li { position: relative; padding-left: 9px; }
  .topics li::before { content: "-"; position: absolute; left: 0; }
</style>
</head>
<body>
<main class="flyer">

  <div class="panel panel--dark" style="left:0;top:0;width:400px;height:320px;"></div>
  <div class="panel panel--light" style="left:0;top:320px;width:400px;height:335px;"></div>
  <div class="panel panel--white" style="left:400px;top:0;width:400px;height:655px;"></div>
  <div class="panel panel--dark" style="left:800px;top:210px;width:400px;height:445px;"></div>
  <div class="panel panel--light" style="left:400px;top:655px;width:800px;height:193px;"></div>
  <div class="photo-warehouse" role="img" aria-label="Foto: zwei Mitarbeitende mit Warnwesten und Helmen in einem Hochregallager"></div>
  <div class="photo-truck" role="img" aria-label="Foto: grüner Sattelzug mit bedruckter Plane auf einer Straße"></div>

  <!-- Modul 1 -->
  <section class="on-dark">
    <div class="num" style="left:25px;top:28px;">1</div>
    <h2 class="title" style="left:59px;top:46px;">Eco Training und Assistenzsysteme</h2>
    <div class="rule on-dark" style="left:43px;top:74px;width:357px;"></div>
    <div class="price" style="left:196px;top:84px;">effektiv ab 40€ netto p. P.*</div>
    <div class="rule on-dark" style="left:196px;top:101px;width:204px;"></div>
    <div class="copy" style="left:49px;top:121px;">
      <p><span class="modul-label">Modul 1</span> nach dem BKrFQG &nbsp;|&nbsp; <b>Dauer:</b> 8 Stunden<br>Weiterbildung nach dem BKrFQG für Güterverkehr<br>Klasse C/CE und Personenverkehr Klasse D/DE</p>
      <p>Durch das Seminar optimieren die Fahrer-/innen<br>Ihren Fahrstil zur Reduzierung des Kraftstoffver-<br>brauchs. Zusätzlich mindern die Fahrer/-innen durch<br>das Eco Training den Verschleiß am Fahrzeug. Sie<br>erwerben die notwendigen Kenntnisse für ökono-<br>misches Fahren.</p>
    </div>
  </section>

  <!-- Modul 2 -->
  <section>
    <h2 class="title" style="left:51px;top:354px;">Sozialvorschriften und<br>Fahrtenschreiber</h2>
    <div class="num" style="left:337px;top:358px;">2</div>
    <div class="rule" style="left:0;top:404px;width:338px;"></div>
    <div class="price" style="left:51px;top:413px;">effektiv ab 40€ netto p. P.*</div>
    <div class="rule" style="left:0;top:430px;width:202px;"></div>
    <div class="copy" style="left:51px;top:451px;">
      <p><span class="modul-label">Modul 2</span> nach dem BKrFQG &nbsp;|&nbsp; <b>Dauer:</b> 8 Stunden<br>Berufskraftfahrer Weiterbildung für Güterverkehr<br>Klasse C/CE und Personenverkehr Klasse D/DE</p>
      <p>Seminarinhalte sind die allgemeinen Vorschriften<br>für den gewerblichen Güterverkehr, Vorschriften<br>zu Lenk- und Ruhezeiten, sowie das Auffrischen von<br>Verkehrsregeln. Um rechtlich auf dem aktuellen<br>Stand zu sein und Gefahren zu senken, sind diese<br>Kenntnisse Voraussetzung.</p>
    </div>
  </section>

  <!-- Modul 3 -->
  <section>
    <div class="num" style="left:429px;top:30px;">3</div>
    <h2 class="title" style="left:583px;top:46px;">Gefahrenwahrnehmung</h2>
    <div class="rule" style="left:560px;top:75px;width:240px;"></div>
    <div class="price" style="left:601px;top:84px;">effektiv ab 40€ netto p. P.*</div>
    <div class="rule" style="left:601px;top:101px;width:199px;"></div>
    <div class="copy" style="left:451px;top:121px;">
      <p><span class="modul-label">Modul 3</span> nach dem BKrFQG &nbsp;|&nbsp; <b>Dauer:</b> 8 Stunden<br>Berufskraftfahrer Weiterbildung für Güterverkehr<br>Klasse C/CE und Personenverkehr Klasse D/DE</p>
      <p>Die Fahrer-/innen erweitern Ihre Kenntnisse hinsicht-<br>lich neuer Sicherheitstechniken an den Fahrzeugen.<br>Sie lernen, diese richtig zu bedienen und einzusetzen.<br>Themenschwerpunkt ist das Kennenlernen moderner<br>Fahrzeugtechnik.</p>
    </div>
  </section>

  <!-- Modul 4 -->
  <section>
    <h2 class="title" style="left:451px;top:290px;">Schadensprävention</h2>
    <div class="num" style="left:732px;top:271px;">4</div>
    <div class="rule" style="left:400px;top:320px;width:368px;"></div>
    <div class="price" style="left:451px;top:329px;">effektiv ab 40€ netto p. P.*</div>
    <div class="rule" style="left:400px;top:347px;width:200px;"></div>
    <div class="copy" style="left:451px;top:365px;">
      <p><span class="modul-label">Modul 4</span> nach dem BKrFQG &nbsp;|&nbsp; <b>Dauer:</b> 8 Stunden<br>Berufskraftfahrer Weiterbildung für Güterverkehr<br>Klasse C/CE und Personenverkehr Klasse D/DE</p>
      <p>Im Seminar wird erläutert, wie Fahrer-/innen durch<br>Ihr Verhalten aktiv dazu beitragen können, ein<br>positives Firmenimage aufzubauen. Weitere Themen<br>sind: Gesundheit und Ergometrie, Alkohol, Drogen<br>und Medikamente am Steuer, richtiges Verhalten im<br>Notfall und in Notsituationen sowie Kriminalität und<br>Schleusung illegaler Einwanderer.</p>
    </div>
    <div class="note-box">*&nbsp;&nbsp;&nbsp;&nbsp; bis zu 70% Kostenersparnis durch ESF-Förderung,<br>kofinanziert von der Europäischen Union</div>
  </section>

  <!-- Modul 6 -->
  <section class="on-dark">
    <div class="num" style="left:829px;top:218px;">6</div>
    <h2 class="title" style="left:953px;top:233px;">Ausbildung Ladungssicherung</h2>
    <div class="rule on-dark" style="left:860px;top:265px;width:340px;"></div>
    <div class="price" style="left:1006px;top:272px;">effektiv ab 102€ netto p. P. *</div>
    <div class="rule on-dark" style="left:999px;top:291px;width:201px;"></div>
    <div class="copy" style="left:843px;top:296px;">
      <p>Ausbildung Ladungssicherung für alle am Transport<br>beteiligten Personengruppen nach VDI 2700a &nbsp;&nbsp;|<br><b>Dauer:</b> 16 Stunden - Theorie und Praxis<br>Ordnungsgemäße Ladungssicherung führt zur Reduz-<br>ierung von Transportschäden, Reduzierung von Unfall-<br>und Folgekosten, sowie Vermeidung von Bußgeldern.</p>
      <ul class="topics tight">
        <li>Rechtliche Grundlagen</li>
        <li>Verordnung sowie Richtlinien zur Ladungssicherung</li>
        <li>Physikalische Grundlagen</li>
        <li>Ladungssicherung bei Fahrzeugen<br>mit offener Ladefläche</li>
        <li>Ladungssicherung bei Handwerker-<br>und Werkstattfahrzeugen</li>
        <li>Ladungssicherung bei Fahrzeugen<br>mit Kastenaufbau</li>
        <li>Ladungssicherung im Kurier-,<br>Express-, Paketdienst</li>
        <li>Tipps und Irrtümer der Ladungssicherung</li>
        <li>Praxisanwendungen der Sicherungs-<br>und Hilfsmittel für Transporter</li>
      </ul>
    </div>
  </section>

  <!-- Modul 5 -->
  <section>
    <div class="num" style="left:431px;top:686px;">5</div>
    <h2 class="title" style="left:597px;top:704px;">Ladungssicherung für Ladung und Fahrgast</h2>
    <div class="rule" style="left:462px;top:732px;width:738px;"></div>
    <div class="price" style="left:996px;top:704px;">effektiv ab 40€ netto p. P.*</div>
    <div class="rule" style="left:992px;top:721px;width:208px;"></div>
    <div class="copy" style="left:451px;top:752px;">
      <p><span class="modul-label">Modul 5</span> nach dem BKrFQG &nbsp;|&nbsp; <b>Dauer:</b> 8 Stunden<br>Berufskraftfahrer Weiterbildung für Güterverkehr Klasse<br>C/CE und Personenverkehr Klasse D/DE</p>
    </div>
    <div class="copy" style="left:833px;top:750px;">
      <p>In diesem Seminar vertiefen die Fahrer-/innen ihre<br>Kenntnisse zu Sicherheitsvorschriften und physikalischen<br>Gesetzen. Sie lernen, Ihre Ladung unter Anwendung von<br>Zurrmitteln und Zurrtechniken richtig zu verladen.</p>
    </div>
  </section>

</main>
</body>
</html>
```